University Social app needs Instagram layout help - tile layout and designs for 18 different types

We need a instagram profile look for our app Tindleloop that is getting a new look and feel. We want 18 different tiles designs that mesh well and look good together on the profile page. This can be a mix of images and text. Tindleloop is based in Sydney, Australia and is a Social app that helps students connect IRL ,find new friends and activities/experiences through society campus events. Topics can include but not limited to the following: Whats on, society spotlight, how to use Tindleloop, Tindleloop features, memes, Helpful hits, POV, Uni Life IRL, Make the Connection, Try Something New, Tindleloop Community, Student Voice, Uni 101, Tindleloop It, Student Stories. please also see current Tindleloop instagram page for content type ideas. It also needs to have the new Tindleloop brand colours (#04ccd9 with a gradient to white background) (also see attached file). The final tiles should communicate university fun, connection and a place to find events. Swap out the current stickers for activity based stickers similar to the attached examples to demonstrate that the app is for finding fun events and activities and for connection.
Look and feel
Each slider illustrates characteristics of the customer's brand and the style your logo design should communicate.

```html
<!DOCTYPE html>
<html lang="en">
<head>
<meta charset="utf-8">
<title>Tindleloop – Instagram Tile Set</title>
<link rel="stylesheet" href="https://fonts.googleapis.com/css2?family=Permanent+Marker&family=Poppins:wght@400;500;600;800&display=swap">
<style>
  :root{
    --brand:#04ccd9;
    --brand-soft:#6ee6ef;
    --brand-pale:#e9fbfd;
    --ink:#0d0d0d;
    --paper:#ffffff;
    --stage:#e7e5e4;
    --accent:#ffe100;
    --photo-dark:#5d6463;
    --photo-light:#c9cfcd;
  }
  *{box-sizing:border-box;margin:0;padding:0}
  html,body{width:1200px;height:800px;overflow:hidden}
  body{background:var(--stage);font-family:"Poppins",sans-serif;color:var(--ink);position:relative}
  .tile{position:absolute;width:272px;height:272px;overflow:hidden;background:var(--paper)}
  .tile--gradient{background:linear-gradient(180deg,var(--paper) 0%,var(--brand-pale) 20%,var(--brand-soft) 100%)}
  .abs{position:absolute}
  .dots{position:absolute;display:grid;grid-template-columns:repeat(4,2px);gap:7px}
  .dots span{width:2px;height:2px;border-radius:50%;background:var(--ink)}
  .brand-name{position:absolute;left:0;right:0;text-align:center;font-weight:600;font-size:19px;letter-spacing:.2px}
  .script{position:absolute;font-family:"Permanent Marker",cursive;color:var(--ink);white-space:nowrap;line-height:1}
  .brush{position:absolute;height:5px;border-radius:3px;background:var(--brand);transform:rotate(-2deg)}

  .tile--events{left:146px;top:108px}
  .tile--community{left:146px;top:426px}
  .tile--post{left:464px;top:256px}
  .tile--whats-on{left:782px;top:106px}
  .tile--helpful{left:782px;top:426px}

  .headline{position:absolute;left:76px;top:44px;font-weight:800;font-size:27px;line-height:.96}
  .highlight{position:absolute;left:60px;top:150px;width:198px;height:52px;background:var(--accent);transform:rotate(-2deg);border-radius:3px}
  .script--friends{left:72px;top:144px;font-size:29px;line-height:.92;transform:rotate(-3deg)}
  .body-copy{position:absolute;left:38px;right:38px;top:162px;font-size:7px;line-height:1.3;text-align:center}
  .tagline{position:absolute;left:0;right:0;top:146px;text-align:center;font-size:17px;line-height:1.22;font-weight:400}
  .section-title{position:absolute;left:0;right:0;text-align:center;top:40px;font-weight:800;font-size:27px}
  .rule{position:absolute;left:34px;width:204px;height:1.5px;background:var(--ink)}
  .photo{position:absolute;left:0;right:0;top:92px;bottom:0;background:linear-gradient(180deg,var(--photo-light) 0%,#9aa2a0 45%,var(--photo-dark) 100%)}
</style>
</head>
<body>

<section class="tile tile--gradient tile--events">
  <div class="abs" style="right:-54px;top:-54px;width:110px;height:110px;border-radius:50%;background:var(--brand-soft)"></div>
  <h2 class="headline">Find<br>events,<br>join<br>societies</h2>
  <div class="highlight"></div>
  <p class="script script--friends">make new<br>friends</p>
  <div class="dots" style="left:22px;top:210px"><span></span><span></span><span></span><span></span><span></span><span></span><span></span><span></span><span></span><span></span><span></span><span></span><span></span><span></span><span></span><span></span></div>
  <p class="brand-name" style="top:222px">Tindleloop</p>
  <div class="abs" style="left:14px;bottom:-20px;width:40px;height:40px;border-radius:50%;background:var(--ink)"></div>
</section>

<section class="tile tile--community">
  <div class="abs" style="right:28px;top:-18px;width:38px;height:38px;border-radius:50%;background:var(--ink)"></div>
  <div class="abs" style="left:0;top:126px;width:18px;height:36px;background:var(--brand)"></div>
  <div class="dots" style="right:30px;top:30px"><span></span><span></span><span></span><span></span><span></span><span></span><span></span><span></span><span></span><span></span><span></span><span></span><span></span><span></span><span></span><span></span></div>
  <svg class="abs" style="left:100px;top:46px" width="72" height="44" viewBox="0 0 72 44" aria-label="Community icon" role="img">
    <g fill="none" stroke="var(--ink)" stroke-width="3.5">
      <circle cx="13" cy="11" r="6"/><circle cx="36" cy="8" r="6"/><circle cx="59" cy="11" r="6"/>
    </g>
    <path d="M3 40c0-12 4-20 10-20s10 8 10 20M26 40c0-14 4-23 10-23s10 9 10 23M49 40c0-12 4-20 10-20s10 8 10 20" fill="var(--brand)" stroke="var(--ink)" stroke-width="3.5"/>
  </svg>
  <p class="script" style="left:68px;top:96px;font-size:32px;transform:rotate(-3deg)">Community</p>
  <div class="brush" style="left:70px;top:132px;width:136px"></div>
  <p class="body-copy">Meet students who share your interests, join campus societies and turn every event into a new friendship. Your uni crew is one tap away, so come along and say hi.</p>
  <p class="brand-name" style="top:222px">Tindleloop</p>
  <div class="abs" style="right:0;top:228px;width:40px;height:16px;border-radius:8px 0 0 8px;background:var(--ink)"></div>
</section>

<section class="tile tile--post" style="background:linear-gradient(180deg,var(--paper) 0%,var(--brand-pale) 40%,var(--brand-soft) 100%)">
  <div class="photo" role="img" aria-label="Black and white photo of students sitting on the grass having a picnic by the harbour, with yellow spark accents"></div>
  <div class="abs" style="left:-20px;top:16px;width:40px;height:40px;border-radius:50%;background:var(--ink)"></div>
  <div class="dots" style="left:30px;top:20px"><span></span><span></span><span></span><span></span><span></span><span></span><span></span><span></span><span></span><span></span><span></span><span></span><span></span><span></span><span></span><span></span></div>
  <p class="brand-name" style="left:auto;right:26px;top:24px">Tindleloop</p>
</section>

<section class="tile tile--whats-on">
  <div class="abs" style="left:0;top:0;width:40px;height:44px;background:var(--brand)"></div>
  <div class="abs" style="right:38px;top:-10px;width:16px;height:50px;border-radius:8px;background:var(--ink)"></div>
  <svg class="abs" style="left:117px;top:50px" width="46" height="44" viewBox="0 0 46 44" role="img" aria-label="Calendar icon">
    <rect x="3" y="7" width="40" height="34" rx="6" fill="none" stroke="var(--ink)" stroke-width="3"/>
    <line x1="3" y1="16" x2="43" y2="16" stroke="var(--ink)" stroke-width="3"/>
    <line x1="14" y1="2" x2="14" y2="11" stroke="var(--ink)" stroke-width="3" stroke-linecap="round"/>
    <line x1="32" y1="2" x2="32" y2="11" stroke="var(--ink)" stroke-width="3" stroke-linecap="round"/>
    <g fill="var(--brand)"><rect x="9" y="21" width="5" height="4"/><rect x="17" y="21" width="5" height="4"/><rect x="25" y="21" width="5" height="4"/><rect x="33" y="21" width="5" height="4"/><rect x="9" y="29" width="5" height="4"/><rect x="17" y="29" width="5" height="4"/><rect x="25" y="29" width="5" height="4"/></g>
  </svg>
  <p class="script" style="left:80px;top:104px;font-size:30px;transform:rotate(-3deg)">Whats On?</p>
  <div class="brush" style="left:78px;top:136px;width:136px"></div>
  <p class="tagline">Find the best<br>events near you</p>
  <svg class="abs" style="left:116px;top:200px" width="46" height="14" viewBox="0 0 46 14" role="img" aria-label="Arrow">
    <path d="M2 7h40M34 2l8 5-8 5" fill="none" stroke="var(--brand)" stroke-width="3" stroke-linecap="round" stroke-linejoin="round"/>
  </svg>
  <div class="dots" style="left:26px;top:222px"><span></span><span></span><span></span><span></span><span></span><span></span><span></span><span></span><span></span><span></span><span></span><span></span><span></span><span></span><span></span><span></span></div>
  <div class="abs" style="left:68px;top:218px;width:40px;height:40px;border-radius:50%;background:var(--ink);clip-path:inset(0 50% 0 0)"></div>
  <div class="abs" style="left:180px;bottom:0;width:36px;height:18px;background:var(--brand)"></div>
</section>

<section class="tile tile--gradient tile--helpful">
  <div class="abs" style="left:6px;top:-20px;width:40px;height:40px;border-radius:50%;background:var(--ink)"></div>
  <div class="dots" style="left:12px;top:30px"><span></span><span></span><span></span><span></span><span></span><span></span><span></span><span></span><span></span><span></span><span></span><span></span><span></span><span></span><span></span><span></span></div>
  <h2 class="section-title">Helpful Hits</h2>
  <div class="abs" style="left:50px;top:78px;width:168px;height:4px;border-radius:2px;background:var(--brand)"></div>
  <div class="rule" style="top:112px"></div>
  <div class="rule" style="top:147px"></div>
  <div class="rule" style="top:182px"></div>
  <div class="rule" style="top:214px"></div>
  <div class="abs" style="right:0;top:230px;width:40px;height:16px;border-radius:8px 0 0 8px;background:var(--ink)"></div>
  <div class="abs" style="left:32px;bottom:0;width:36px;height:18px;background:var(--paper)"></div>
</section>

</body>
</html>
```